Business Card Design for BrightvaleMedia.com

--I need a business card design for my company BrightvaleMedia.com

I have attached my logo...I want the brightvale media logo on the front of the business card, and then I want The Quillstone Chief on the back of it with my information.

I would like to see a light colored background as well as a dark colored background

FRONT:
BRIGHTVALE MEDIA LOGO
248 N. Larkmoor
3rd Floor
San Diego CA 92173
www.BrightvaleMedia.com

Advanced Website & App Development
Websites, Apps, Online Voucher Systems

Leading Edge Marketing Services
SMS, VB, SMM, SEM,

BACK:
QUILLSTONE CHIEF LOGO
Dorian Pelletta
The Quillstone Chief
Call Or Text: 619-555-0148
Dorian@QuillstoneChief.example
www.QuillstoneChief.example

Target Market(s)

small business owners

Industry/Entity Type

Business Consultant

Contact Information for Business Card

FRONT:
BRIGHTVALE MEDIA LOGO
248 N. Larkmoor
3rd Floor
San Diego CA 92173
www.BrightvaleMedia.com

SMS, VB, SMM, SEM,

BACK:
QUILLSTONE CHIEF LOGO
Dorian Pelletta
The Quillstone Chief
Dorian@QuillstoneChief.example
www.QuillstoneChief.example

Requirements
Must have
• add this quote on it somewhere, anywhere,preferrably on back
• "The Fastest Way To Success Is To Take Action”
• — Dorian Pelletta, Quillstone Chief
Nice to have
• open
Should not have
• red

```html
<!DOCTYPE html>
<html lang="en">
<head>
<meta charset="utf-8">
<title>Brightvale Media Business Cards</title>
<link rel="stylesheet" href="https://fonts.googleapis.com/css2?family=Montserrat:wght@400;600;700&family=Oswald:wght@500&display=swap">
<style>
  :root {
    --backdrop: #e4e6e8;
    --card-white: #ffffff;
    --card-grey: #6d6e71;
    --card-blue: #1470ab;
    --brand-blue: #1a6faf;
    --ink: #3a3a3c;
    --on-dark: #ffffff;
  }
  * { margin: 0; padding: 0; box-sizing: border-box; }
  html, body { width: 1200px; height: 927px; overflow: hidden; }
  body {
    background: var(--backdrop);
    font-family: "Montserrat", sans-serif;
    position: relative;
  }
  .card {
    position: absolute;
    top: 240px;
    width: 255px;
    height: 446px;
    text-align: center;
    box-shadow: 0 2px 6px rgba(0,0,0,0.12);
  }
  .card--back-1 { left: 33px; background: var(--card-white); }
  .card--front-1 { left: 312px; background: var(--card-grey); }
  .card--back-2 { left: 635px; background: var(--card-white); }
  .card--front-2 { left: 912px; background: var(--card-blue); }

  .wordmark {
    position: absolute;
    top: 34px;
    left: 0; right: 0;
    font-weight: 600;
    font-size: 20px;
    letter-spacing: 0.5px;
    line-height: 1.2;
  }
  .wordmark--chief { color: var(--brand-blue); }
  .wordmark--media { color: var(--on-dark); }
  .wordmark span { display: block; font-size: 12px; letter-spacing: 5px; margin-top: 4px; }

  .tagline {
    position: absolute;
    top: 72px;
    left: 0; right: 0;
    font-family: "Oswald", sans-serif;
    font-weight: 500;
    font-size: 12.5px;
    color: var(--brand-blue);
    letter-spacing: 0.1px;
  }

  .contact {
    position: absolute;
    top: 322px;
    left: 50%;
    transform: translateX(-50%);
    width: 210px;
  }
  .rule {
    height: 2px;
    width: 160px;
    margin: 0 auto;
    background: linear-gradient(90deg, transparent, var(--brand-blue) 20%, var(--brand-blue) 80%, transparent);
    opacity: 0.8;
  }
  .contact__name {
    margin-top: 5px;
    font-size: 17px;
    font-weight: 600;
    color: var(--brand-blue);
  }
  .contact__role { font-size: 10.5px; color: var(--ink); margin-top: 1px; }
  .contact__lines {
    margin: 9px 0 5px;
    font-size: 11px;
    line-height: 14px;
    color: var(--ink);
  }
  .contact__lines b { color: var(--brand-blue); font-weight: 600; }
  .contact__lines .site { color: var(--brand-blue); font-weight: 600; }

  .details {
    position: absolute;
    top: 284px;
    left: 0; right: 0;
    color: var(--on-dark);
    font-size: 11px;
    line-height: 13.6px;
  }
  .details p + p { margin-top: 6px; }
  .details strong { font-weight: 700; }
  .details .services { font-weight: 600; letter-spacing: 0.2px; line-height: 14px; }
</style>
</head>
<body>

  <section class="card card--back-1">
    <div class="wordmark wordmark--chief">QUILLSTONE CHIEF</div>
    <p class="tagline">THE FASTEST WAY TO SUCCESS IS TO TAKE ACTION</p>
    <div class="contact">
      <div class="rule"></div>
      <p class="contact__name">Dorian Pelletta</p>
      <p class="contact__role">CEO</p>
      <p class="contact__lines">
        <b>P:</b> 619-555-0148<br>
        <b>E:</b> Dorian@QuillstoneChief.example<br>
        <b>W:</b> www.<span class="site">QuillstoneChief</span>.example
      </p>
      <div class="rule"></div>
    </div>
  </section>

  <section class="card card--front-1">
    <div class="wordmark wordmark--media">BRIGHTVALE MEDIA</div>
    <div class="details">
      <p>248 N. Larkmoor<br>3rd Floor<br>San Diego CA 92173<br>www.<strong>BrightvaleMedia</strong>.com</p>
      <p>Advanced Website &amp; App Development<br>Websites, Apps, Online Voucher Systems</p>
      <p class="services">LEADING EDGE MARKETING SERVICES<br>SMS, VB, SMM, SEM,</p>
    </div>
  </section>

  <section class="card card--back-2">
    <div class="wordmark wordmark--chief">QUILLSTONE CHIEF</div>
    <p class="tagline">THE FASTEST WAY TO SUCCESS IS TO TAKE ACTION</p>
    <div class="contact">
      <div class="rule"></div>
      <p class="contact__name">Dorian Pelletta</p>
      <p class="contact__role">CEO</p>
      <p class="contact__lines">
        <b>P:</b> 619-555-0148<br>
        <b>E:</b> Dorian@QuillstoneChief.example<br>
        <b>W:</b> www.<span class="site">QuillstoneChief</span>.example
      </p>
      <div class="rule"></div>
    </div>
  </section>

  <section class="card card--front-2">
    <div class="wordmark wordmark--media">BRIGHTVALE MEDIA</div>
    <div class="details">
      <p>248 N. Larkmoor<br>3rd Floor<br>San Diego CA 92173<br>www.<strong>BrightvaleMedia</strong>.com</p>
      <p>Advanced Website &amp; App Development<br>Websites, Apps, Online Voucher Systems</p>
      <p class="services">LEADING EDGE MARKETING SERVICES<br>SMS, VB, SMM, SEM,</p>
    </div>
  </section>

</body>
</html>
```